Stylish Business Cards Wanted

- DOUBLE SIDED Design Required -

High end, edgy cards for a corporate and personal stylist. Must include logo,
Name: Belinda Harwick
Title: Director and Stylist
telephone : +61 8 7142 5809
email: belinda@theloombriefing.example
website: theloombriefing.example
Tag: Corporate Workwear & Uniform Specialist | Personal Stylist
Would like nice icons for telephone, email, website

Target Market(s)

Businesses wanting stylish uniforms, people wanting stylish wardrobes

Industry/Entity Type

Corporate Workwear Stylist

Contact Information for Business Card

I would like black, white and gold foiling incorporated in the design - possibly a touch of the other colours on my branding guide attached Name: Belinda Harwick Title: Director and Stylist telephone : +61 8 7142 5809 email: belinda@theloombriefing.example website: theloombriefing.example Tag: Corporate Workwear & Uniform Specialist | Personal Stylist Would like nice icons for telephone, email, website

Font styles to use
Other font styles liked:
• Raleway

Colors

Designer to choose colors to be used in the design.

Requirements
Must have
• Gold foil accents

```html
<!DOCTYPE html>
<html lang="en">
<head>
<meta charset="utf-8">
<title>The Loom Briefing — Business Card</title>
<link href="https://fonts.googleapis.com/css2?family=Roboto:wght@400;700&family=Courgette&family=Dancing+Script:wght@500&display=swap" rel="stylesheet">
<style>
  :root {
    --backdrop: #3b3b3c;
    --card: #1b1b1d;
    --gold: #d9ad38;
    --white: #f4f4f4;
  }
  * { margin: 0; padding: 0; box-sizing: border-box; }
  html, body {
    width: 799px; height: 1200px; overflow: hidden;
    background: var(--backdrop);
  }
  .canvas {
    position: relative; width: 799px; height: 1200px;
  }
  .card {
    position: absolute; left: 80px; width: 640px; height: 366px;
    background: var(--card); border-radius: 28px;
    box-shadow: 0 10px 30px rgba(0,0,0,.45);
  }
  .card--front { top: 117px; }
  .card--back { top: 717px; }

  .front-brand {
    position: absolute; inset: 0;
    display: flex; align-items: center; justify-content: center;
    font-family: "Roboto", sans-serif; font-weight: 700;
    font-size: 52px; letter-spacing: 1px; color: var(--gold);
  }

  .holder { position: absolute; left: 48px; top: 52px; }
  .holder-name {
    font-family: "Courgette", cursive; font-size: 30px; color: var(--gold);
    line-height: 1.1;
  }
  .holder-title {
    font-family: "Roboto", sans-serif; font-size: 13px; color: var(--white);
    margin-top: 4px;
  }

  .contact-list {
    position: absolute; left: 48px; top: 204px; list-style: none;
    font-family: "Roboto", sans-serif; font-size: 15px; color: var(--white);
  }
  .contact-item { display: flex; align-items: center; gap: 10px; height: 23px; }
  .contact-icon { width: 14px; height: 14px; flex: none; }

  .tagline {
    position: absolute; left: 48px; top: 290px;
    font-family: "Dancing Script", cursive; font-weight: 500;
    font-size: 20px; color: var(--white);
  }
  .tagline-divider { color: var(--gold); margin: 0 8px; font-family: "Roboto", sans-serif; font-size: 16px; }

  .back-brand {
    position: absolute; right: 44px; top: 130px;
    font-family: "Roboto", sans-serif; font-weight: 700;
    font-size: 30px; color: var(--white); text-align: center; line-height: 1.05;
  }
</style>
</head>
<body>
<main class="canvas">
  <section class="card card--front" aria-label="Card front">
    <div class="front-brand">The Loom Briefing</div>
  </section>

  <section class="card card--back" aria-label="Card back">
    <div class="holder">
      <h1 class="holder-name">Belinda Harwick</h1>
      <p class="holder-title">Director and Stylist</p>
    </div>

    <ul class="contact-list">
      <li class="contact-item">
        <svg class="contact-icon" viewBox="0 0 16 16" aria-hidden="true">
          <circle cx="8" cy="8" r="7" fill="none" stroke="var(--gold)" stroke-width="1.4"/>
          <path d="M5.3 4.6l1.3-.3.8 1.8-.9.7c.4.9 1.1 1.6 2 2l.7-.9 1.8.8-.3 1.3c-3 .2-5.6-2.4-5.4-5.4z" fill="var(--gold)"/>
        </svg>
        <span>+61 8 7142 5809</span>
      </li>
      <li class="contact-item">
        <svg class="contact-icon" viewBox="0 0 16 16" aria-hidden="true">
          <rect x="1.5" y="3.5" width="13" height="9" fill="none" stroke="var(--gold)" stroke-width="1.4"/>
          <path d="M1.5 3.5L8 9l6.5-5.5" fill="none" stroke="var(--gold)" stroke-width="1.4"/>
        </svg>
        <span>belinda@theloombriefing.example</span>
      </li>
      <li class="contact-item">
        <svg class="contact-icon" viewBox="0 0 16 16" aria-hidden="true">
          <circle cx="8" cy="8" r="6.5" fill="none" stroke="var(--gold)" stroke-width="1.4"/>
          <ellipse cx="8" cy="8" rx="2.8" ry="6.5" fill="none" stroke="var(--gold)" stroke-width="1.2"/>
          <path d="M1.5 8h13M2.5 5h11M2.5 11h11" stroke="var(--gold)" stroke-width="1.1"/>
        </svg>
        <span>www.theloombriefing.example</span>
      </li>
    </ul>

    <p class="tagline">Corporate Workwear &amp; Uniform Specialist<span class="tagline-divider">|</span>Personal Stylist</p>

    <div class="back-brand">The Loom<br>Briefing</div>
  </section>
</main>
</body>
</html>
```